Tidy paddock Services

After a high quality design website. we are a company that provides services to people that own land and need a hand getting on top of the delayed jobs.
would want a number of tab/ pages for the web page.
Home page / About us page / services page / Gallery page. / Contact us page
we offer a wide range of services .listed below

Stock Work (title)

Stock movement
Break feeding
Temporary staffing

Spraying (title)

Spraying weeds
Spraying gorse

Pastures (title)

Fertilizing
Topping

Building (title)

Habitable sheds
Farm sheds
Sheep yards
Cattle yards
Repair farm buildings
Decks
Retaining walls

Fencing (title)

Stock fencing
Post & rail
Stock yards repair
Electric fencing install & repairs

Water Management (title)

Water trough installation
Water scheme install
Water trough cleaning
Farm water maintenance
Water ponds
Ornamental ponds
Drainage

General (title)

Lawn mowing
Hedge trimming
Pruning trees
Metaling drive ways & races
Water blasting
Small digger work
Little tip truck cartage
Home kill management
Mulching gorse
Section clearing

```html
<!DOCTYPE html>
<html lang="en">
<head>
<meta charset="utf-8">
<title>Tidy paddock Services</title>
<link href="https://fonts.googleapis.com/css2?family=Lato:wght@400;700;900&family=Roboto:wght@300;400;700&display=swap" rel="stylesheet">
<style>
:root{
  --green:#6aa319;
  --green-dark:#4f8a0f;
  --green-light:#7cb82a;
  --black:#0b0b0b;
  --ink:#1a1a1a;
  --grey-text:#555;
  --soft-bg:#f4f4f4;
  --white:#fff;
}
*{margin:0;padding:0;box-sizing:border-box}
html,body{width:1200px;height:4329px;overflow:hidden}
body{position:relative;font-family:'Lato',sans-serif;color:var(--ink);background:var(--white)}
.abs{position:absolute}
a{color:inherit;text-decoration:none}

/* header */
.header{left:0;top:0;width:1200px;height:103px;background:var(--white)}
.brand{display:flex;align-items:center;gap:10px}
.brand-dot{width:26px;height:26px;border-radius:50%;background:var(--green)}
.brand-name{font-family:'Lato',sans-serif;font-weight:700;color:var(--green);font-size:19px;line-height:1.05;text-transform:uppercase}
.header .brand{left:110px;top:30px}
.quote-btn{left:549px;top:28px;width:153px;height:47px;border-radius:24px;background:var(--green);color:#fff;font-weight:700;font-size:13px;display:flex;align-items:center;justify-content:center}
.social{display:flex;gap:7px}
.social span{width:36px;height:36px;border-radius:50%;background:#fff;box-shadow:0 2px 8px rgba(0,0,0,.18)}
.header .social{left:742px;top:34px}
.call-panel{left:850px;top:0;width:350px;height:153px}
.call-icon{left:988px;top:31px;width:50px;height:50px;border-radius:50%;background:#fff;display:flex;align-items:center;justify-content:center}
.call-label{left:1052px;top:47px;color:#fff;font-weight:700;font-size:14px}
.call-number{left:945px;top:88px;color:#fff;font-weight:700;font-size:28px}
.nav{left:0;top:103px;width:850px;height:50px;background:var(--black);display:flex;align-items:center;padding-left:110px;gap:36px}
.nav a{color:#fff;font-weight:700;font-size:13px}
.nav a.active{color:var(--green-light)}
.nav-strip{left:0;top:103px;width:1200px;height:50px;background:var(--black)}

/* hero */
.hero{left:0;top:153px;width:1200px;height:643px;background:linear-gradient(90deg,#5e6a2c 0%,#8a8b3a 30%,#6f6a44 55%,#4f7a2a 80%,#3f6a22 100%)}
.hero::after{content:"";position:absolute;inset:0;background:linear-gradient(180deg,rgba(0,0,0,.1) 0%,rgba(0,0,0,.25) 50%,rgba(60,110,20,.25) 100%)}
.hero-copy{left:0;top:170px;width:1200px;text-align:center;color:#fff;z-index:2}
.hero-title{font-family:'Roboto',sans-serif;font-weight:700;font-size:58px;line-height:1.2;text-shadow:0 2px 6px rgba(0,0,0,.4)}
.hero-title .light{font-weight:300;display:block}
.hero-sub{font-size:23px;line-height:33px;margin-top:18px;text-shadow:0 2px 6px rgba(0,0,0,.4)}
.hero-btn{display:inline-block;margin-top:26px;padding:0 28px;height:46px;line-height:46px;border-radius:24px;background:var(--green);color:#fff;font-weight:700;font-size:14px}
.dots{left:560px;top:745px;display:flex;gap:12px;align-items:center;z-index:2}
.dots span{width:7px;height:7px;border-radius:50%;background:#fff}
.dots span.on{width:22px;height:22px;border:2px solid #fff;background:transparent;position:relative}
.dots span.on::after{content:"";position:absolute;left:5px;top:5px;width:8px;height:8px;border-radius:50%;background:#fff}

/* section titles */
.sec-title{left:0;width:1200px;text-align:center;font-family:'Roboto',sans-serif;font-size:46px;font-weight:700;color:var(--ink)}
.sec-title .accent{font-weight:400;color:var(--green)}

/* services */
.service{width:310px;text-align:center}
.service-ring{width:310px;height:310px;border-radius:50%;border:4px solid #9a9a9a;padding:11px}
.service-ring.featured{border-color:var(--green)}
.service-photo{width:100%;height:100%;border-radius:50%}
.service-name{margin-top:30px;font-weight:700;font-size:20px}
.plus{width:34px;height:34px;border-radius:50%;background:var(--green);margin:18px auto 0;display:flex;align-items:center;justify-content:center}
.arrow{width:30px;height:30px;display:flex;align-items:center;justify-content:center}

/* about */
.about{left:0;top:1620px;width:1200px;height:566px;background:linear-gradient(180deg,#6aa319 0%,#5f9a16 60%,#4f8a0f 100%)}
.about-ring{left:111px;top:1686px;width:434px;height:434px;border-radius:50%;border:6px solid #fff;padding:14px}
.about-photo{width:100%;height:100%;border-radius:50%;background:linear-gradient(180deg,#9cc3e6 0%,#dfe9f1 40%,#7a9a4a 62%,#4d7a26 100%)}
.about-title{left:598px;top:1696px;font-family:'Roboto',sans-serif;font-size:42px;font-weight:700;color:#fff}
.about-title .light{font-weight:400}
.about-text{left:598px;top:1782px;width:490px;color:#fff;font-size:15px;line-height:27.5px;text-align:justify}
.about-text p+p{margin-top:16px}
.learn-btn{left:598px;top:2050px;width:147px;height:48px;border-radius:24px;background:var(--black);color:#fff;font-weight:900;font-size:13px;display:flex;align-items:center;justify-content:center}

/* testimonials */
.clients{left:0;top:2186px;width:1200px;height:566px;background:var(--soft-bg)}
.card{top:2374px;width:305px;height:276px;background:#fff;box-shadow:0 2px 10px rgba(0,0,0,.1);padding:26px 23px}
.stars{color:#f2a91c;font-size:15px;letter-spacing:1px}
.card p{margin-top:10px;font-size:15px;line-height:27.5px;color:var(--grey-text)}
.card hr{border:0;border-top:1px solid #ddd;margin:14px 0 18px}
.person{display:flex;align-items:center;gap:18px}
.avatar{width:58px;height:58px;border-radius:50%;background:linear-gradient(135deg,#c9b9a6,#8a7563)}
.person-name{font-weight:700;font-size:14px}
.person-loc{font-size:12px;color:var(--green);margin-top:6px;font-weight:700}
.round-arrow{width:36px;height:36px;border-radius:50%;display:flex;align-items:center;justify-content:center}

/* gallery */
.gallery-tile{}

/* footer */
.footer{left:0;top:3720px;width:1200px;height:609px;background:var(--black)}
.news-title{left:0;top:3800px;width:1200px;text-align:center;font-family:'Roboto',sans-serif;font-size:36px;font-weight:700;color:#fff}
.news-title .accent{font-weight:400;color:var(--green-light)}
.news-input{left:209px;top:3886px;width:627px;height:48px;border:2px solid #fff;border-radius:24px;color:#fff;font-size:14px;display:flex;align-items:center;padding-left:24px}
.news-btn{left:844px;top:3886px;width:147px;height:48px;border-radius:24px;background:var(--green);color:#fff;font-weight:900;font-size:15px;display:flex;align-items:center;justify-content:center}
.rule{left:111px;width:977px;height:1px;background:#333}
.footer .brand{left:115px;top:4106px}
.footer .brand-dot{width:34px;height:34px}
.footer .brand-name{font-size:27px}
.col-title{color:#fff;font-weight:700;font-size:17px}
.col-list{list-style:none;margin-top:16px}
.col-list li{color:#fff;font-size:14px;height:38px;display:flex;align-items:flex-start;gap:20px}
.col-list li::before{content:"";width:4px;height:4px;border-radius:50%;background:var(--green-light);margin-top:7px;flex:none}
.contact-list{list-style:none;margin-top:16px}
.contact-list li{color:#fff;font-size:14px;line-height:22px;display:flex;gap:14px;margin-bottom:14px}
.contact-list svg{flex:none;margin-top:4px}
.copyright{left:0;top:4280px;width:1200px;text-align:center;color:#fff;font-size:13px}
.copyright b{font-weight:900}
.foot-social{left:966px;top:4272px;display:flex;gap:7px}
.foot-social span{width:36px;height:36px;border-radius:50%;border:2px solid var(--green)}
.foot-social span.fill{background:var(--green)}
</style>
</head>
<body>

<!-- Header -->
<header class="abs header">
  <div class="abs brand"><span class="brand-dot"></span><span class="brand-name">Tidy paddock<br>Services</span></div>
  <a class="abs quote-btn" href="#">GET A QUOTE</a>
  <div class="abs social" aria-label="Social links"><span></span><span></span><span></span></div>
</header>
<div class="abs nav-strip"></div>
<svg class="abs call-panel" width="350" height="153" viewBox="0 0 350 153"><polygon points="135,0 350,0 350,153 0,153" fill="#6aa319"/></svg>
<div class="abs call-icon"><svg width="20" height="20" viewBox="0 0 24 24"><path d="M6.6 10.8a15.1 15.1 0 0 0 6.6 6.6l2.2-2.2c.3-.3.7-.4 1-.2 1.1.4 2.3.6 3.6.6.6 0 1 .4 1 1V20c0 .6-.4 1-1 1C10.6 21 3 13.4 3 4c0-.6.4-1 1-1h3.5c.6 0 1 .4 1 1 0 1.3.2 2.5.6 3.6.1.3 0 .7-.2 1z" fill="#1a1a1a"/></svg></div>
<div class="abs call-label">CALL US TODAY:</div>
<div class="abs call-number">+1 (555) 014 2290</div>
<nav class="abs nav">
  <a class="active" href="#">HOME</a><a href="#">ABOUT US</a><a href="#">SERVICES</a><a href="#">GALLERY</a><a href="#">CONTACT US</a>
</nav>

<!-- Hero -->
<section class="abs hero" role="img" aria-label="Worker pushing a lawn mower across a green lawn"></section>
<div class="abs hero-copy">
  <h1 class="hero-title">TIDY PADDOCK<span class="light">SERVICES</span></h1>
  <p class="hero-sub">Lorem ipsum dolor sit amet, consectetur adipiscing<br>sed do eiusmod temporea.</p>
  <a class="hero-btn" href="#">CONTACT US</a>
</div>
<div class="abs dots"><span></span><span class="on"></span><span></span><span></span></div>

<!-- Services -->
<h2 class="abs sec-title" style="top:908px">OUR <span class="accent">SERVICES</span></h2>
<div class="abs arrow" style="left:36px;top:1153px"><svg width="16" height="26" viewBox="0 0 16 26"><path d="M13 2 3 13l10 11" stroke="#6aa319" stroke-width="3.5" fill="none" stroke-linecap="round"/></svg></div>
<div class="abs arrow" style="left:1132px;top:1153px"><svg width="16" height="26" viewBox="0 0 16 26"><path d="M3 2l10 11L3 24" stroke="#6aa319" stroke-width="3.5" fill="none" stroke-linecap="round"/></svg></div>

<div class="abs service" style="left:111px;top:1013px">
  <div class="service-ring"><div class="service-photo" role="img" aria-label="Worker writing on a clipboard beside boxes" style="background:linear-gradient(160deg,#e9e6e1,#c7b49a 60%,#9a7a58)"></div></div>
  <div class="service-name">STOCK WORK</div>
  <div class="plus"><svg width="12" height="12" viewBox="0 0 12 12"><path d="M6 1v10M1 6h10" stroke="#fff" stroke-width="2.4"/></svg></div>
</div>
<div class="abs service" style="left:445px;top:1013px">
  <div class="service-ring featured"><div class="service-photo" role="img" aria-label="Person in protective suit spraying crops" style="background:linear-gradient(160deg,#b9cf8a,#6f9a3a 55%,#3f6a22)"></div></div>
  <div class="service-name">SPRAYING</div>
  <div class="plus"><svg width="12" height="12" viewBox="0 0 12 12"><path d="M6 1v10M1 6h10" stroke="#fff" stroke-width="2.4"/></svg></div>
</div>
<div class="abs service" style="left:779px;top:1013px">
  <div class="service-ring"><div class="service-photo" role="img" aria-label="Gloved hand spreading fertilizer around a seedling" style="background:linear-gradient(160deg,#6a8a3a,#4a5a2a 55%,#2f2a22)"></div></div>
  <div class="service-name">PASTURES</div>
  <div class="plus"><svg width="12" height="12" viewBox="0 0 12 12"><path d="M6 1v10M1 6h10" stroke="#fff" stroke-width="2.4"/></svg></div>
</div>

<!-- About -->
<section class="abs about"></section>
<div class="abs about-ring"><div class="about-photo" role="img" aria-label="Red barn and silo beside a country road under a cloudy sky"></div></div>
<h2 class="abs about-title">ABOUT <span class="light">US</span></h2>
<div class="abs about-text">
  <p>Lorem ipsum dolor sit amet, consectetur adipiscing elit, sed do eiusmod tempor incididunt ut labore et dolore magna aliqua. Ut enim ad minim veniam, quis nostrud exercitation ullamco laboris nisi ut aliquip ex ea commodo consequat duis aute irure dolor in reprehe nderit in voluptate velit esse cillum dolorea.</p>
  <p>Lorem ipsum dolor sit amet, consectetur adipiscing elit, sed do eiusmod tempor incididunt ut labore et dolore magna aliqua. Ut enim ad minim veniam, quis nostrud exercitation ullamco.</p>
</div>
<a class="abs learn-btn" href="#">LEARN MORE</a>

<!-- Testimonials -->
<section class="abs clients"></section>
<h2 class="abs sec-title" style="top:2274px">WHAT OUR <span class="accent">CLIENTS SAY</span></h2>
<div class="abs round-arrow" style="left:34px;top:2493px;background:#e4e8dc"><svg width="10" height="14" viewBox="0 0 10 14"><path d="M8 1 2 7l6 6" stroke="#6aa319" stroke-width="2.4" fill="none"/></svg></div>
<div class="abs round-arrow" style="left:1130px;top:2493px;background:var(--green)"><svg width="10" height="14" viewBox="0 0 10 14"><path d="M2 1l6 6-6 6" stroke="#fff" stroke-width="2.4" fill="none"/></svg></div>

<article class="abs card" style="left:111px">
  <div class="stars">★★★★★</div>
  <p>Lorem ipsum dolor sit amet, consect adipiscing elit, sed do eiusmod temp incididunt ut labore et dolore magna t enim ad minim veniam.</p>
  <hr>
  <div class="person"><div class="avatar" role="img" aria-label="Client portrait"></div><div><div class="person-name">MARCUS REID</div><div class="person-loc">United States</div></div></div>
</article>
<article class="abs card" style="left:447px">
  <div class="stars">★★★★★</div>
  <p>Lorem ipsum dolor sit amet, consect adipiscing elit, sed do eiusmod temp incididunt ut labore et dolore magna t enim ad minim veniam.</p>
  <hr>
  <div class="person"><div class="avatar" role="img" aria-label="Client portrait" style="background:linear-gradient(135deg,#7a4a30,#3a2418)"></div><div><div class="person-name">HANNAH COLE</div><div class="person-loc">United States</div></div></div>
</article>
<article class="abs card" style="left:783px">
  <div class="stars">★★★★★</div>
  <p>Lorem ipsum dolor sit amet, consect adipiscing elit, sed do eiusmod temp incididunt ut labore et dolore magna t enim ad minim veniam.</p>
  <hr>
  <div class="person"><div class="avatar" role="img" aria-label="Client portrait" style="background:linear-gradient(135deg,#d8d4cc,#8a7a6a)"></div><div><div class="person-name">DANIEL BROOKS</div><div class="person-loc">United States</div></div></div>
</article>

<!-- Gallery -->
<h2 class="abs sec-title" style="top:2874px">OUR <span class="accent">GALLERY</span></h2>
<div class="abs gallery-tile" role="img" aria-label="New timber lattice fence in front of houses" style="left:111px;top:2978px;width:480px;height:321px;background:linear-gradient(180deg,#d9dde0 0%,#c9a46a 45%,#b8884a 75%,#5f8a2a 100%)"></div>
<div class="abs gallery-tile" role="img" aria-label="Irrigation system watering rows of crops" style="left:608px;top:2978px;width:480px;height:321px;background:linear-gradient(135deg,#a9c98a 0%,#4f8a3a 45%,#1f4a2a 100%)"></div>
<div class="abs gallery-tile" role="img" aria-label="Hedge trimming shears cutting a green hedge" style="left:111px;top:3316px;width:315px;height:290px;background:linear-gradient(135deg,#3f6a22 0%,#6f9a3a 55%,#c9d9a0 100%)"></div>
<div class="abs gallery-tile" role="img" aria-label="Lawn mower cutting long grass" style="left:442px;top:3316px;width:316px;height:290px;background:linear-gradient(180deg,#4a6a3a 0%,#5a8a2a 50%,#8ac23a 100%)"></div>
<div class="abs gallery-tile" role="img" aria-label="Water flowing from a pipe into a garden pond" style="left:773px;top:3316px;width:315px;height:290px;background:linear-gradient(135deg,#2a3a1a 0%,#5a6a3a 50%,#2f3a2a 100%)"></div>

<!-- Footer -->
<footer class="abs footer"></footer>
<h2 class="abs news-title">SIGN UP TO <span class="accent">OUR NEWSLETTER</span></h2>
<div class="abs news-input">Enter Email Address</div>
<a class="abs news-btn" href="#">SIGN UP</a>
<div class="abs rule" style="top:3978px"></div>

<div class="abs brand"style="left:115px;top:4100px"><span class="brand-dot" style="width:34px;height:34px"></span><span class="brand-name" style="font-size:27px">Tidy paddock<br>Services</span></div>

<div class="abs" style="left:457px;top:4017px">
  <div class="col-title">NAVIGATION</div>
  <ul class="col-list"><li>Home</li><li>About Us</li><li>Services</li><li>Gallery</li><li>Contact Us</li></ul>
</div>
<div class="abs" style="left:644px;top:4017px">
  <div class="col-title">QUICK LINKS</div>
  <ul class="col-list"><li>Site Map</li><li>FAQ</li><li>Privacy Policy</li><li>Terms Of Use</li></ul>
</div>
<div class="abs" style="left:852px;top:4017px">
  <div class="col-title">CONTACT INFO</div>
  <ul class="contact-list">
    <li><svg width="12" height="14" viewBox="0 0 12 16"><path d="M6 0a6 6 0 0 0-6 6c0 4.5 6 10 6 10s6-5.5 6-10a6 6 0 0 0-6-6zm0 8.2A2.2 2.2 0 1 1 6 3.8a2.2 2.2 0 0 1 0 4.4z" fill="#7cb82a"/></svg><span>465, Lorum Ipsum Dolore Sed,<br>United States</span></li>
    <li><svg width="13" height="13" viewBox="0 0 24 24"><path d="M6.6 10.8a15.1 15.1 0 0 0 6.6 6.6l2.2-2.2c.3-.3.7-.4 1-.2 1.1.4 2.3.6 3.6.6.6 0 1 .4 1 1V20c0 .6-.4 1-1 1C10.6 21 3 13.4 3 4c0-.6.4-1 1-1h3.5c.6 0 1 .4 1 1 0 1.3.2 2.5.6 3.6.1.3 0 .7-.2 1z" fill="#7cb82a"/></svg><span>+1 (555) 014 2290</span></li>
    <li><svg width="14" height="11" viewBox="0 0 16 12"><rect width="16" height="12" rx="1" fill="#7cb82a"/><path d="M1 1l7 6 7-6" stroke="#0b0b0b" stroke-width="1.5" fill="none"/></svg><span>info@tidypaddockservices.com</span></li>
  </ul>
</div>
<div class="abs rule" style="top:4252px"></div>
<div class="abs copyright">© 2024 <b>TIDY PADDOCK SERVICES</b> &nbsp;|&nbsp; All Rights Reserved</div>
<div class="abs foot-social" aria-label="Social links"><span class="fill"></span><span></span><span></span></div>

</body>
</html>
```